Stylish Business Cards Wanted

- DOUBLE SIDED Design Required -

High end, edgy cards for a corporate and personal stylist. Must include logo,
Name: Belinda Harwick
Title: Director and Stylist
telephone : +61 8 7142 5809
email: belinda@theloombriefing.example
website: theloombriefing.example
Tag: Corporate Workwear & Uniform Specialist | Personal Stylist
Would like nice icons for telephone, email, website

Target Market(s)

Businesses wanting stylish uniforms, people wanting stylish wardrobes

Industry/Entity Type

Corporate Workwear Stylist

Contact Information for Business Card

I would like black, white and gold foiling incorporated in the design - possibly a touch of the other colours on my branding guide attached Name: Belinda Harwick Title: Director and Stylist telephone : +61 8 7142 5809 email: belinda@theloombriefing.example website: theloombriefing.example Tag: Corporate Workwear & Uniform Specialist | Personal Stylist Would like nice icons for telephone, email, website

Font styles to use
Other font styles liked:
• Raleway

Colors

Designer to choose colors to be used in the design.

Requirements
Must have
• Gold foil accents

```html
<!DOCTYPE html>
<html lang="en">
<head>
<meta charset="utf-8">
<title>The Loom Briefing — Business Cards</title>
<link href="https://fonts.googleapis.com/css2?family=Open+Sans:ital,wght@0,400;0,700;1,400&display=swap" rel="stylesheet">
<style>
  :root {
    --stage: #2a2a2a;
    --card: #161616;
    --gold: #cdbd82;
    --gold-light: #efe3b0;
    --gold-deep: #a8955a;
  }
  * { margin: 0; padding: 0; box-sizing: border-box; }
  html, body {
    width: 1200px; height: 900px; overflow: hidden;
    background: var(--stage);
    font-family: "Open Sans", sans-serif;
  }
  .sheet {
    width: 1200px; height: 900px;
    display: flex; flex-direction: column;
    align-items: center; justify-content: center; gap: 56px;
  }
  .card {
    position: relative;
    width: 640px; height: 366px;
    background: var(--card);
    border-bottom: 4px solid var(--gold);
    box-shadow: 0 10px 30px rgba(0,0,0,.45);
    color: var(--gold);
    overflow: hidden;
  }
  /* Front */
  .card--front { display: flex; align-items: center; justify-content: center; }
  .wordmark {
    font-size: 50px; font-weight: 700; letter-spacing: 1px;
    color: var(--gold);
  }
  /* Back */
  .card--back { padding: 0 48px; }
  .identity {
    position: absolute; left: 48px; top: 118px; width: 250px;
    text-align: right;
  }
  .identity__name {
    font-size: 23px; font-weight: 700; letter-spacing: .5px;
    text-transform: uppercase; line-height: 1.2;
  }
  .identity__title { font-size: 15px; font-style: italic; margin-top: 4px; }
  .divider {
    position: absolute; left: 318px; top: 110px;
    width: 1px; height: 92px; background: var(--gold-deep);
  }
  .contacts {
    position: absolute; left: 340px; top: 112px;
    list-style: none; font-size: 14px; line-height: 1;
  }
  .contacts li { display: flex; align-items: center; gap: 9px; margin-bottom: 13px; }
  .contacts svg { width: 14px; height: 14px; flex: none; fill: var(--gold); }
  .tagline {
    position: absolute; left: 48px; right: 48px; bottom: 42px;
    font-size: 15px; letter-spacing: .3px; text-align: center;
  }
  .tagline__sep { margin: 0 12px; }
</style>
</head>
<body>
<main class="sheet">
  <section class="card card--front" aria-label="Card front">
    <span class="wordmark">The Loom Briefing</span>
  </section>

  <section class="card card--back" aria-label="Card back">
    <div class="identity">
      <p class="identity__name">Belinda Harwick</p>
      <p class="identity__title">Director and Stylist</p>
    </div>
    <span class="divider"></span>
    <ul class="contacts">
      <li>
        <svg viewBox="0 0 24 24" aria-hidden="true"><path d="M6.6 10.8a15.1 15.1 0 0 0 6.6 6.6l2.2-2.2a1 1 0 0 1 1-.25 11.4 11.4 0 0 0 3.6.57 1 1 0 0 1 1 1V20a1 1 0 0 1-1 1A17 17 0 0 1 3 4a1 1 0 0 1 1-1h3.5a1 1 0 0 1 1 1c0 1.25.2 2.45.57 3.57a1 1 0 0 1-.25 1z"/></svg>
        <span>+61 8 7142 5809</span>
      </li>
      <li>
        <svg viewBox="0 0 24 24" aria-hidden="true"><path d="M2 5h20v14H2z M2 5l10 8 10-8" fill="none" stroke="#cdbd82" stroke-width="2"/></svg>
        <span>belinda@theloombriefing.example</span>
      </li>
      <li>
        <svg viewBox="0 0 24 24" aria-hidden="true"><g fill="none" stroke="#cdbd82" stroke-width="2"><circle cx="12" cy="12" r="9.5"/><ellipse cx="12" cy="12" rx="4" ry="9.5"/><path d="M2.5 12h19"/></g></svg>
        <span>theloombriefing.example</span>
      </li>
    </ul>
    <p class="tagline">Corporate Workwear &amp; Uniform Specialist<span class="tagline__sep">•</span>Personal Stylist</p>
  </section>
</main>
</body>
</html>
```